Make a medical leaflet for my patients undergoing ankle blocks

I have a very boring text only leaflet I would like to turn into a professional appealing medical leaflet to give to my patients. I would like to get this onto two pages of a4 if possible and its intended for electronic distribution mainly.
This will be for patients so it must be professional.
It must also contain a copyright logo on it and my name near the start (Dr Paul Venning) so my colleagues can't use it easily.
Target Market(s)
Patients undergoing surgery
Industry/Entity Type
Medical
Font styles to use
Other font styles liked:
- no idea, you tell me
Requirements
Must have
- the information contained on the attachment
- look professional
- a copyright on it
Nice to have
- the harbour infirmary logo
Should not have
- Any spelling, grammatical or linguistic errors
- Any font less than size 12

```html
<!DOCTYPE html>
<html lang="en">
<head>
<meta charset="utf-8">
<title>Ankle Block – Patient Information Leaflet</title>
<link href="https://fonts.googleapis.com/css2?family=Cabin:wght@400;600;700&display=swap" rel="stylesheet">
<style>
  :root{
    --blue:#1a4fa0;
    --blue-dark:#123d80;
    --ink:#1f2a44;
    --cream:#efe8d8;
    --gold:#b9a77a;
    --backdrop:#a4a4a4;
    --white:#ffffff;
  }
  *{box-sizing:border-box;margin:0;padding:0}
  html,body{width:1007px;height:1200px;overflow:hidden;background:var(--backdrop)}
  body{position:relative;font-family:"Cabin",sans-serif;color:var(--ink)}
  .page{
    position:absolute;top:262px;width:470px;height:665px;overflow:hidden;
    background:linear-gradient(to bottom,var(--white) 0%,var(--white) 70%,var(--cream) 100%);
    box-shadow:0 6px 14px rgba(0,0,0,.35);
  }
  .page--front{left:22px}
  .page--back{left:515px}

  .header{position:relative;height:135px}
  .brand{
    position:absolute;left:0;top:0;width:175px;height:135px;background:var(--blue);
    display:flex;flex-direction:column;align-items:center;justify-content:center;
    color:var(--white);text-align:center;padding:0 18px 20px;
  }
  .brand__mark{width:14px;height:14px;border:1.5px solid var(--white);border-radius:50%;margin-bottom:10px}
  .brand__name{font-size:17px;font-weight:600;line-height:1.25}
  .photo{position:absolute;left:175px;top:0;right:0;height:135px}
  .photo--doctor{background:linear-gradient(120deg,#e7edf4 0%,#c9d4e1 45%,#f1f3f6 100%)}
  .photo--nurse{background:linear-gradient(120deg,#d9cfc5 0%,#efe9e4 40%,#b8c6d6 75%,#cfd8e2 100%)}
  .name-tab{
    position:absolute;right:0;top:14px;background:var(--blue);color:var(--white);
    font-size:11px;font-weight:600;padding:4px 14px 4px 22px;
  }
  .hospital{position:absolute;right:12px;top:58px;text-align:right;color:var(--blue-dark)}
  .hospital__name{font-size:11px;padding-bottom:2px;border-bottom:1px solid var(--blue)}
  .hospital__group{font-size:6px;margin-top:2px}
  .header__wave{position:absolute;left:0;bottom:-1px;width:100%;height:40px}

  .content{padding:4px 24px 0 24px;font-size:7.9px;line-height:1.36}
  .page--back .content{font-size:8.4px;line-height:1.4}
  .content p{margin-bottom:4px}
  h2{
    font-size:10px;font-weight:700;color:var(--blue);display:inline-block;
    padding-right:40px;border-bottom:1px solid var(--gold);margin:8px 0 5px;
  }
  h3{font-size:8.2px;font-weight:700;color:var(--blue);margin:4px 0 2px 4px}
  .band{background:var(--blue);color:var(--white);margin:6px -24px 0;padding:2px 24px 6px}
  .band h2{color:var(--white);border-color:var(--gold);margin-top:2px}
  .band ul{list-style:none}
  .band li::before{content:"• ";color:var(--gold)}
  .ticks{list-style:none;margin:0 0 4px 18px}
  .ticks li{padding-left:11px;position:relative}
  .ticks li::before{content:"✓";position:absolute;left:0;color:var(--blue);font-weight:700}
  .dashes{list-style:none;margin-left:22px}
  .dashes li::before{content:"- "}
  .risks{position:relative}
  .risk{width:330px}
  .portrait{
    position:absolute;right:-6px;top:12px;width:78px;height:142px;
    background:linear-gradient(to bottom,#d9e1ea,#f4f6f8);border-radius:4px;
  }
  .justify{text-align:justify}

  .footer{position:absolute;left:0;bottom:0;width:100%;height:40px}
  .footer svg{position:absolute;left:0;top:0;width:100%;height:100%}
  .footer__url{
    position:absolute;left:0;right:0;bottom:7px;text-align:center;
    color:var(--white);font-size:8px;font-weight:700;
  }
  .footer__copy{position:absolute;left:24px;bottom:8px;color:var(--white);font-size:7px}
</style>
</head>
<body>

<section class="page page--front">
  <header class="header">
    <div class="brand">
      <span class="brand__mark"></span>
      <span class="brand__name">The Harbour Infirmary</span>
    </div>
    <div class="photo photo--doctor" role="img" aria-label="Photograph of a consultant reviewing notes beside a patient in a hospital bed"></div>
    <div class="name-tab">Dr Paul Venning</div>
    <div class="hospital">
      <div class="hospital__name">Riverside Park Hospital</div>
      <div class="hospital__group">part of Meridian Health Group</div>
    </div>
    <svg class="header__wave" viewBox="0 0 470 40" preserveAspectRatio="none">
      <path d="M0 22 C120 40 300 40 470 6 L470 40 L0 40 Z" fill="#fff"/>
      <path d="M0 22 C120 40 300 40 470 6" fill="none" stroke="#1a4fa0" stroke-width="3"/>
    </svg>
  </header>

  <div class="content">
    <h2>Ankle block</h2>
    <p class="justify">You are scheduled to have surgery on your foot. It is my normal practice to offer and perform (with your consent) an ankle block. This is an optional injection of numbing liquid to the nerves which supply your foot. The ankle block can be performed when you are awake, sedated or under general anaesthesia.</p>
    <p class="justify">The ankle block can be combined with a general anaesthetic and with sedation. It can also be used to allow surgery to be performed with you wide awake in certain cases.</p>
    <p class="justify">Having or not having an ankle block does not change the pre operative fasting guidelines you have been given.</p>
    <p class="justify">There is a fee for performing an ankle block. Please consult my initial introductory email and terms of business for details.</p>

    <div class="band">
      <h2>What are the benefits</h2>
      <ul>
        <li>Excellent pain relief - usually 10 - 14 hours (and rarely 24 - 48 hours)</li>
        <li>Avoiding traditional painkillers, resulting in less post operative nausea and vomiting</li>
        <li>The option to avoid a general anaesthetic (if you wish)</li>
        <li>A faster recovery from the general anaesthetic</li>
        <li>Certain surgery requires an overnight stay in hospital without an ankle block</li>
      </ul>
    </div>

    <h2>What are the risks?</h2>
    <p>As with all injections, there is the risk of bruising, bleeding and infection.</p>
    <div class="risks">
      <div class="risk">
        <h3>1 - Nerve Damage -</h3>
        <ul class="ticks">
          <li>Occurs 1 in 5000 nerve blocks.</li>
          <li>Creates an area of numbness or weakness/paralysis in some / all the foot.</li>
          <li>The majority of nerve injuries will heal themselves within a year.</li>
          <li>There is no treatment to fix it.</li>
          <li>If the block has not worn off after 72 hours please let me know.</li>
        </ul>
        <h3>2 - Failure -</h3>
        <ul class="ticks">
          <li>The success rate with ankle blocks is 98 - 99%.</li>
          <li>Some blocks will fail, partially or totally.</li>
          <li>If total failure, I will discuss repeating the block with your consent.</li>
        </ul>
        <h3>3 - Pain during operation -</h3>
        <ul class="ticks">
          <li>If you choose to have wide awake surgery or surgery under sedation, the surgery will stop and I will discuss three options with you:</li>
        </ul>
        <ul class="dashes">
          <li>more numbing liquid to be injected by the surgeon</li>
          <li>more sedation / painkiller</li>
          <li>having a general anaesthetic</li>
        </ul>
      </div>
      <div class="portrait" role="img" aria-label="Photograph of a smiling doctor in a white coat with arms folded"></div>
    </div>
    <p style="margin-top:4px">If you decide to undergo surgery awake or sedated, there is a risk you will need to have a general anaesthetic if you feel pain. This is why the starvation instructions of awake surgery and general anaesthesia are the same.</p>
  </div>

  <footer class="footer">
    <svg viewBox="0 0 470 40" preserveAspectRatio="none">
      <path d="M0 10 C160 2 320 2 470 12 L470 40 L0 40 Z" fill="#1a4fa0"/>
      <path d="M0 6 C160 -2 320 -2 470 8" fill="none" stroke="#1a4fa0" stroke-width="1.5"/>
      <path d="M0 16 C160 8 320 8 470 18" fill="none" stroke="#ffffff" stroke-width="1.2"/>
    </svg>
    <div class="footer__copy">© Dr Paul Venning</div>
    <div class="footer__url">www.theharbourinfirmary.co.uk</div>
  </footer>
</section>

<section class="page page--back">
  <header class="header">
    <div class="brand">
      <span class="brand__mark"></span>
      <span class="brand__name">The Harbour Infirmary</span>
    </div>
    <div class="photo photo--nurse" role="img" aria-label="Photograph of a nurse attending a smiling patient on a hospital ward"></div>
    <svg class="header__wave" viewBox="0 0 470 40" preserveAspectRatio="none">
      <path d="M0 22 C120 40 300 40 470 6 L470 40 L0 40 Z" fill="#fff"/>
      <path d="M0 22 C120 40 300 40 470 6" fill="none" stroke="#1a4fa0" stroke-width="3"/>
    </svg>
  </header>

  <div class="content">
    <h2>How is it done</h2>
    <h3>If you choose awake surgery or surgery with sedation -</h3>
    <ul class="ticks">
      <li>Numbing liquid is injected around the nerves which supply your foot.</li>
      <li>The ankle block takes 5 - 10 minutes to perform and requires 4 - 5 injections.</li>
      <li>It takes approximately 10 - 20 minutes to make your foot numb to pain.</li>
      <li>I will check the ankle block is working before we start surgery using cold spray.</li>
      <li>Sensations of touch, pressure, vibration and movement will still be felt.</li>
      <li>I will use a screen so you can't see the surgery (unless you would like to see).</li>
      <li>Some patients bring headphones to block out the noise of the operation.</li>
    </ul>
    <h3>If you choose a General anaesthetic -</h3>
    <ul class="ticks">
      <li>I will perform the ankle block after I start the general anaesthetic.</li>
      <li>You should wake up from your surgery with a comfortable and numb foot.</li>
      <li>If you wake in pain, we can repeat the ankle block or provide traditional painkillers.</li>
    </ul>
    <p class="justify">Whichever you choose, there will be a cannula placed in your hand, and heart and oxygen monitoring throughout.</p>

    <h2>After surgery</h2>
    <p class="justify">You will go to the recovery area and then onto the ward when you are ready. It will be difficult to walk while the block is working, so physiotherapists will help you first walk. If you need crutches, they will teach you how to use them.</p>
    <p class="justify">Your foot will be numb and so you will not feel where your foot is in relation to nearby objects. As a result, it is easy to knock your foot. Please take extra care while your foot is still numb.</p>
    <p class="justify">As the block wears off, the foot may feel slightly painful, tingly or hot. At this point you should take your painkillers I have prescribed. Depending on your medical history you will have up to three painkillers. I would suggest to start with all three. You will also have an anti-sickness prescribed if one of the painkillers (typically codeine or morphine) makes you feel sick.</p>
    <p class="justify">Occasionally (1 - 2%), pain when the block wears off will be severe. In this case contact your surgeon's secretary. We can use stronger pain medication, but there will be a charge in writing and getting the private prescription to you (please see my terms of business) via courier.</p>

    <h2>The alternative</h2>
    <ul class="ticks">
      <li>If you do not have an ankle block, your surgery can still proceed.</li>
      <li>Post operative pain can be managed with traditional painkillers.</li>
      <li>However, you are more likely to need an overnight stay or feel sick after the anaesthetic.</li>
    </ul>
    <p class="justify">If you have any further questions about an ankle block, I will see you on the day of your surgery. Alternatively, you can request the following optional services (as mentioned in my terms of business).</p>
  </div>

  <footer class="footer">
    <svg viewBox="0 0 470 40" preserveAspectRatio="none">
      <path d="M0 10 C160 2 320 2 470 12 L470 40 L0 40 Z" fill="#1a4fa0"/>
      <path d="M0 6 C160 -2 320 -2 470 8" fill="none" stroke="#1a4fa0" stroke-width="1.5"/>
      <path d="M0 16 C160 8 320 8 470 18" fill="none" stroke="#ffffff" stroke-width="1.2"/>
    </svg>
    <div class="footer__copy">© Dr Paul Venning</div>
    <div class="footer__url">www.theharbourinfirmary.co.uk</div>
  </footer>
</section>

</body>
</html>
```